Velk Partners Building Business Cards

We need a business card that reflects our business as "Solar Experts" in San Diego. Browse our website www.velkpartners.example our License needs to be displayed as "CSLB# 3867140" our phone number is (619) 555-0187

Save thousands on your electric bills and increase the value of your home while helping to protect the environment. Our solar installation experts will help you design the system that's right for you, using only the highest quality equipment that will look great and give you ideal performance. Our goal is to make you energy independent, and get your electric bill to 0.

Paul Osterby
(619) 555-0187
paul@velkpartners.example

Target Market(s)

Home owners in san diego looking for solar

Industry/Entity Type

Solar Energy

Contact Information for Business Card

Paul Osterby
(619) 555-0187
paul@velkpartners.example

Font styles to use
Other font styles liked:
• Use our logo font

Requirements
Must have
• License needs to be displayed as "CSLB# 3867140" our phone number is (619) 555-0187
Nice to have
• Real images of rooftop home solar in san diego
Should not have
• our business address

```html
<!DOCTYPE html>
<html lang="en">
<head>
<meta charset="utf-8">
<title>Velk Partners Building – Business Cards</title>
<link rel="stylesheet" href="https://fonts.googleapis.com/css2?family=Open+Sans:ital,wght@0,400;0,600;1,400&display=swap">
<style>
  :root {
    --navy: #173b72;
    --sun: #f4a71d;
    --ink: #4a4a4a;
    --rule: #c9c9c9;
    --paper: #ffffff;
    --backdrop: #3c3c3c;
  }
  * { margin: 0; padding: 0; box-sizing: border-box; }
  html, body {
    width: 1105px;
    height: 1200px;
    overflow: hidden;
    background: var(--backdrop);
    font-family: "Open Sans", Arial, sans-serif;
  }
  .card {
    position: absolute;
    left: 193px;
    width: 720px;
    height: 410px;
  }
  .card--front { top: 167px; background: var(--paper); }
  .card--back  { top: 623px; background: var(--navy); }

  .wordmark {
    position: absolute;
    display: flex;
    align-items: center;
    gap: 10px;
    font-weight: 600;
    white-space: nowrap;
  }
  .wordmark__dot {
    flex: none;
    border-radius: 50%;
    background: var(--sun);
  }
  .card--front .wordmark {
    left: 40px;
    top: 180px;
    width: 330px;
    justify-content: center;
    font-size: 22px;
    color: var(--navy);
  }
  .card--front .wordmark__dot { width: 18px; height: 18px; }

  .divider {
    position: absolute;
    left: 384px;
    top: 109px;
    width: 1px;
    height: 200px;
    background: var(--rule);
  }

  .contact {
    position: absolute;
    left: 417px;
    top: 113px;
    color: var(--ink);
  }
  .contact__name {
    font-size: 25px;
    font-weight: 600;
    color: var(--navy);
    line-height: 1.2;
  }
  .contact__role {
    font-size: 19px;
    color: var(--sun);
    line-height: 1.2;
  }
  .contact__license {
    margin-top: 18px;
    font-size: 18px;
  }
  .contact__list {
    list-style: none;
    margin-top: 16px;
    font-size: 18px;
    line-height: 28px;
  }
  .contact__list li {
    display: flex;
    align-items: center;
    gap: 10px;
  }
  .contact__list svg { width: 16px; height: 16px; fill: var(--navy); flex: none; }

  .card--back .wordmark {
    left: 0;
    top: 160px;
    width: 720px;
    justify-content: center;
    font-size: 38px;
    color: #ffffff;
    gap: 16px;
  }
  .card--back .wordmark__dot { width: 30px; height: 30px; }

  .back__url {
    position: absolute;
    left: 0;
    top: 337px;
    width: 720px;
    text-align: center;
    font-size: 19px;
    font-style: italic;
    letter-spacing: 6px;
    color: #ffffff;
  }
</style>
</head>
<body>

<section class="card card--front" aria-label="Business card front">
  <div class="wordmark">
    <span class="wordmark__dot"></span>
    <span class="wordmark__name">Velk Partners Building Inc</span>
  </div>

  <div class="divider"></div>

  <div class="contact">
    <p class="contact__name">Paul Osterby</p>
    <p class="contact__role">CEO/Founder</p>
    <p class="contact__license">CSLB# 3867140</p>
    <ul class="contact__list">
      <li>
        <svg viewBox="0 0 16 16" aria-hidden="true"><path d="M3.6 1.2l2.2 2.6c.4.4.3 1-.1 1.4L4.6 6.3c.9 2 2.6 3.8 4.8 4.9l1.1-1.2c.4-.4 1-.5 1.4-.1l2.6 2.1c.4.4.5 1 .1 1.4l-1.3 1.4c-.6.6-1.5.8-2.3.5C6.3 13.6 2.6 9.8 1 5.1.7 4.3.9 3.4 1.5 2.8l1-1.4c.3-.4.8-.5 1.1-.2z"/></svg>
        <span>(619) 555-0187</span>
      </li>
      <li>
        <svg viewBox="0 0 16 16" aria-hidden="true"><path d="M1 3.5h14v1L8 9 1 4.5z"/><path d="M1 6l7 4.5L15 6v7H1z"/></svg>
        <span>paul@velkpartners.example</span>
      </li>
      <li>
        <svg viewBox="0 0 16 16" aria-hidden="true"><path d="M8 1a7 7 0 1 0 0 14A7 7 0 0 0 8 1zm0 1.6c.9 0 1.9 1.7 2.2 4.4H5.8C6.1 4.3 7.1 2.6 8 2.6zM2.7 7h1.6c.1 1.6.4 3 .9 4a5.4 5.4 0 0 1-2.5-4zm0 2h-.1zm8.1 4c.5-1 .8-2.4.9-4h1.6a5.4 5.4 0 0 1-2.5 4zM5.8 9h4.4c-.3 2.7-1.3 4.4-2.2 4.4S6.1 11.7 5.8 9zm5.9-2c-.1-1.6-.4-3-.9-4a5.4 5.4 0 0 1 2.5 4z"/></svg>
        <span>www.velkpartners.example</span>
      </li>
    </ul>
  </div>
</section>

<section class="card card--back" aria-label="Business card back">
  <div class="wordmark">
    <span class="wordmark__dot"></span>
    <span class="wordmark__name">Velk Partners Building Inc</span>
  </div>
  <p class="back__url">www.velkpartners.example</p>
</section>

</body>
</html>
```